Simple and Clean business card design

We would like the design to be simple clean and to incorporate our colors.

We are open to your design and talent, we have the dots in our logo as we think of it as data points and we connect data points for people.

We are open to see the great creative and clean design you bring to the table

Contact Information for Business Card

please include: name, position, email, phone and website

Font styles to use
Sans Serif

Requirements
Must have
• my colors incorporated, simplicity
Nice to have
• lots of white space, simplicity
Should not have
• complexicity/ complex art

```html
<!DOCTYPE html>
<html lang="en">
<head>
<meta charset="utf-8">
<title>Quorra Business Card</title>
<link rel="stylesheet" href="https://fonts.googleapis.com/css2?family=Montserrat:wght@600&family=Lato:wght@700&family=Roboto:wght@400&display=swap">
<style>
  :root {
    --backdrop: #a3a3a3;
    --white: #ffffff;
    --ink: #111111;
    --green: #34a853;
    --yellow: #fbbc05;
    --orange: #f7701e;
    --red: #ea4335;
    --blue: #4285f4;
    --rule: #777777;
  }
  * { box-sizing: border-box; margin: 0; padding: 0; }
  html, body { width: 1200px; height: 1200px; overflow: hidden; }
  body { background: var(--backdrop); position: relative; font-family: "Roboto", Arial, sans-serif; }

  .card { position: absolute; top: 303px; width: 368px; height: 594px; }

  .card-front {
    left: 200px;
    background: linear-gradient(140deg, var(--orange) 0%, var(--yellow) 30%, var(--green) 62%, var(--blue) 95%);
  }
  .card-back { left: 600px; background: var(--white); }

  .wordmark {
    position: absolute; left: 0; right: 0;
    display: flex; justify-content: center; align-items: center; gap: 8px;
    font-family: "Montserrat", Arial, sans-serif; font-weight: 600;
    font-size: 76px; line-height: 1; letter-spacing: -1px;
  }
  .wordmark-dot { width: 18px; height: 18px; border-radius: 50%; }
  .card-front .wordmark { top: 458px; color: var(--white); }
  .card-front .wordmark-dot { background: var(--white); }
  .card-back .wordmark { top: 150px; color: var(--ink); }
  .card-back .wordmark-dot { background: var(--blue); }

  .contact-block { position: absolute; left: 0; right: 0; top: 382px; text-align: center; }
  .person-name {
    font-family: "Lato", Arial, sans-serif; font-weight: 700;
    font-size: 28px; color: var(--blue); line-height: 1;
  }
  .person-role { margin-top: 6px; font-size: 17px; color: var(--ink); }

  .icon-row { margin-top: 14px; display: flex; justify-content: center; align-items: center; gap: 4px; }
  .icon-row .rule { width: 22px; height: 1px; background: var(--rule); margin: 0 2px; }
  .icon { width: 25px; height: 25px; border-radius: 50%; display: flex; align-items: center; justify-content: center; }
  .icon-phone { background: var(--green); }
  .icon-mail { background: var(--yellow); }
  .icon-web { background: var(--red); }

  .contact-lines { margin-top: 10px; font-size: 17px; color: var(--ink); line-height: 25px; }
</style>
</head>
<body>

  <section class="card card-front" role="img" aria-label="Colourful background of soft overlapping translucent circles in orange, yellow, green and blue">
    <div class="wordmark"><span>Quorra</span><span class="wordmark-dot"></span></div>
  </section>

  <section class="card card-back">
    <div class="wordmark"><span>Quorra</span><span class="wordmark-dot"></span></div>

    <div class="contact-block">
      <h1 class="person-name">DANA MERCER</h1>
      <p class="person-role">Founder/ CEO</p>

      <div class="icon-row">
        <span class="rule"></span>
        <span class="icon icon-phone">
          <svg width="13" height="13" viewBox="0 0 24 24" fill="none" stroke="#fff" stroke-width="2.4" stroke-linecap="round" stroke-linejoin="round"><path d="M5 3h4l2 5-2.5 1.5a11 11 0 0 0 6 6L16 13l5 2v4a2 2 0 0 1-2 2A17 17 0 0 1 3 5a2 2 0 0 1 2-2z"/></svg>
        </span>
        <span class="icon icon-mail">
          <svg width="14" height="14" viewBox="0 0 24 24" fill="none" stroke="#fff" stroke-width="2.2" stroke-linejoin="round"><rect x="3" y="6" width="18" height="12"/><path d="M3 6l9 7 9-7"/></svg>
        </span>
        <span class="icon icon-web">
          <svg width="14" height="14" viewBox="0 0 24 24" fill="none" stroke="#fff" stroke-width="2"><circle cx="12" cy="12" r="9"/><path d="M3 12h18M12 3c3 3 3 15 0 18M12 3c-3 3-3 15 0 18"/></svg>
        </span>
        <span class="rule"></span>
      </div>

      <div class="contact-lines">
        <p class="contact-phone">555-214-0387</p>
        <p class="contact-email">dana.mercer@quorra.one</p>
        <p class="contact-web">www.Quorra.one</p>
      </div>
    </div>
  </section>

</body>
</html>
```